Modern Verdell Tree Care Website

I need a website for a full service Tree Care company. The company provides tree pruning, tree removal, tree preservation, emergency services, stump grinding, and emergency tree services.

Target Market(s)

Customers that need tree services

Industry/Entity Type

Landscaping, Tree Services

Coding

Coded - Design and coding required

Number of Pages Required

5+ page

Font styles to use
Sans Serif

Requirements
Must have
• Good clean design that showcases the services the company provides.
Nice to have
• Services page; contact form, blog, home page, about page

```html
<!DOCTYPE html>
<html lang="en">
<head>
<meta charset="utf-8">
<title>Verdell Tree Care</title>
<link href="https://fonts.googleapis.com/css2?family=Poppins:wght@300;400;500;600;700&display=swap" rel="stylesheet">
<style>
:root{
  --green:#8dc63f;
  --green-dark:#6fa52a;
  --slate:#5b686e;
  --tan:#c4966b;
  --orange:#f8ab35;
  --text:#444b4e;
  --muted:#777;
  --white:#fff;
  --field:#f4f4f4;
}
*{box-sizing:border-box;margin:0;padding:0}
html,body{width:1200px;height:5137px;overflow:hidden}
body{position:relative;font-family:'Poppins',sans-serif;color:var(--text);background:var(--white)}
.abs{position:absolute}
a{text-decoration:none;color:inherit}

/* header */
.site-header{left:0;top:0;width:1200px;height:106px;background:var(--white)}
.brand{display:flex;align-items:center;gap:12px;font-weight:600;font-size:26px;color:var(--slate);letter-spacing:.5px}
.brand-mark{width:36px;height:36px;background:var(--green);border-radius:4px}
.site-header .brand{position:absolute;left:72px;top:30px}
.main-nav{position:absolute;right:72px;top:44px;display:flex;gap:34px;font-size:12px;font-weight:500;color:var(--text)}
.main-nav .active{color:var(--green);position:relative}
.main-nav .active::after{content:"";position:absolute;left:-10px;right:-10px;top:28px;height:2px;background:var(--green)}

/* hero */
.hero{left:0;top:106px;width:1200px;height:742px;background:linear-gradient(180deg,#7c8a5a 0%,#4c6a2a 35%,#5d7a2c 60%,#6c8f39 100%)}
.hero-text{left:0;top:246px;width:1200px;text-align:center;color:var(--white)}
.hero-title{font-size:52px;font-weight:600;text-shadow:0 2px 6px rgba(0,0,0,.35)}
.hero-sub{font-size:30px;font-weight:400;margin-top:8px;text-shadow:0 2px 4px rgba(0,0,0,.3)}
.btn-outline-green{display:inline-block;margin-top:18px;width:196px;height:52px;line-height:48px;border:2px solid var(--white);border-radius:26px;background:var(--green);font-size:14px;font-weight:500}

.features{left:110px;top:764px;width:980px;height:166px;display:flex}
.feature{flex:1;display:flex;flex-direction:column;align-items:center;padding-top:28px;color:var(--white);font-size:11.5px;font-weight:600;text-align:center;line-height:1.3}
.feature svg{margin-bottom:14px}
.f-tan{background:var(--tan)}.f-green{background:var(--green)}.f-orange{background:var(--orange)}.f-slate{background:var(--slate)}

/* section titles */
.section-title{text-align:center}
.section-title h2{font-size:50px;font-weight:600;color:var(--slate);line-height:1}
.section-title .kicker{display:flex;align-items:center;justify-content:center;gap:16px;color:var(--green);font-size:18px;letter-spacing:2px;margin-top:4px}
.kicker .rule{width:74px;height:2px;background:var(--green);position:relative}
.kicker .rule.r::after,.kicker .rule.l::before{content:"";position:absolute;top:-3px;width:8px;height:8px;border-radius:50%;background:var(--green)}
.kicker .rule.l::before{right:0}.kicker .rule.r::after{left:0}

/* services */
.service-card{width:300px;height:418px;background:var(--white);border-radius:14px;box-shadow:0 0 10px rgba(0,0,0,.16);padding:8px}
.service-icon{margin:14px 0 0 18px;width:80px;height:80px}
.service-card h3{font-size:20px;font-weight:500;color:#222;margin:12px 0 0 14px}
.service-photo{position:absolute;left:8px;right:8px;bottom:8px;height:244px;border-radius:10px}

/* about */
.about-head h2{font-size:46px;font-weight:600;color:var(--slate);line-height:1}
.about-head .kicker{justify-content:flex-start;font-size:17px;margin-top:2px}
.about-copy{font-size:12.5px;line-height:2.15;color:var(--text);width:560px}
.about-copy p+p{margin-top:26px}
.btn-green{display:inline-block;background:var(--green);color:var(--white);border-radius:26px;text-align:center;font-weight:500}

/* cta */
.cta{left:0;top:2656px;width:1200px;height:472px;background:linear-gradient(90deg,#8dc63f 0%,#86c03b 42%,#5f8a2d 62%,#3d3a2e 85%,#5c4a35 100%)}
.cta h2{color:var(--white);font-size:43px;font-weight:600;line-height:1.3;text-transform:uppercase}
.btn-white{display:block;width:248px;height:72px;line-height:72px;background:var(--white);color:var(--green-dark);border-radius:36px;text-align:center;font-size:21px;font-weight:600}

/* blog */
.post-card{width:280px;height:458px;background:var(--white);border-radius:12px;box-shadow:0 0 10px rgba(0,0,0,.15);padding:8px}
.post-photo{height:204px;border-radius:10px}
.post-body{padding:22px 16px 0}
.post-date{font-size:12px;color:#555;display:flex;align-items:center;gap:6px}
.post-date i{display:inline-block;width:11px;height:11px;background:var(--green);border-radius:2px}
.post-body h3{font-size:15px;font-weight:500;color:#222;line-height:1.45;margin-top:10px}
.post-body p{font-size:11.5px;color:var(--muted);line-height:1.85;margin-top:12px}
.post-body .btn-green{width:108px;height:28px;line-height:28px;font-size:11px;margin-top:16px}
.dots{display:flex;gap:10px;align-items:center}
.dots span{width:12px;height:12px;border-radius:50%;background:#d0d0d0}
.dots .on{width:28px;height:8px;border-radius:4px;background:var(--orange)}

/* contact */
.contact-photo{left:102px;top:4100px;width:424px;height:442px;border-radius:12px;background:linear-gradient(180deg,#dfe7d6 0%,#6b7d5a 45%,#3d5330 100%)}
.field{background:var(--white);border:1px solid #e4e4e4;box-shadow:0 0 6px rgba(0,0,0,.08);font-size:12px;color:#999;padding:14px 20px}

/* footer */
.site-footer{left:0;top:4660px;width:1200px;height:477px;background:var(--green)}
.newsletter{left:206px;top:4714px;width:788px;height:108px;border-radius:54px;background:var(--orange);border:3px solid #fbc36b}
.newsletter h3{position:absolute;left:34px;top:30px;font-size:30px;font-weight:500;color:var(--white)}
.nl-form{position:absolute;left:412px;top:34px;width:352px;height:38px;background:var(--white);border-radius:19px;font-size:9px;color:#555;padding:12px 22px}
.nl-form span{position:absolute;right:0;top:0;width:104px;height:38px;border-radius:19px;background:var(--green);color:var(--white);font-size:13px;font-weight:500;text-align:center;line-height:38px}
.foot-h{font-size:17px;font-weight:600;color:var(--white)}
.quick-links{list-style:none;color:var(--white);font-size:13px}
.quick-links li{display:flex;align-items:center;gap:12px;height:27px}
.quick-links li::before{content:"";width:9px;height:9px;border-radius:50%;background:var(--white)}
.footer-brand{left:396px;top:4906px;font-size:50px;font-weight:600;color:var(--white);display:flex;align-items:center;gap:18px;letter-spacing:1px}
.footer-brand .brand-mark{width:70px;height:70px;background:var(--white);border-radius:6px}
.contact-item{display:flex;gap:14px;color:var(--white);font-size:12px;line-height:1.35;margin-bottom:12px}
.contact-item i{flex:none;width:26px;height:26px;border-radius:50%;background:var(--orange)}
.bottom-bar{left:0;top:5088px;width:1200px;height:49px;background:#7fb33a;color:var(--white);font-size:11px}
.socials{position:absolute;right:72px;top:12px;display:flex;gap:6px}
.socials span{width:26px;height:26px;border-radius:50%;border:1.5px solid var(--white)}
</style>
</head>
<body>

<header class="site-header abs">
  <div class="brand"><span class="brand-mark"></span>Verdell Tree Care</div>
  <nav class="main-nav">
    <a class="active">HOME</a><a>ABOUT US</a><a>SERVICES ▾</a><a>BLOG</a><a>CONTACT US</a>
  </nav>
</header>

<section class="hero abs" role="img" aria-label="Large spreading oak tree on a green lawn with a person walking nearby"></section>
<div class="hero-text abs">
  <h1 class="hero-title">Call Verdell for All Your Tree Care Needs</h1>
  <p class="hero-sub">Serving Lafayette and surrounding areas</p>
  <a class="btn-outline-green">LEARN MORE</a>
</div>

<div class="features abs">
  <div class="feature f-tan"><svg width="58" height="58" viewBox="0 0 58 58"><circle cx="29" cy="29" r="26" fill="none" stroke="#fff" stroke-width="3"/><path d="M19 30l7 7 14-16" fill="none" stroke="#fff" stroke-width="3"/></svg>LICENSED AND INSURED</div>
  <div class="feature f-green"><svg width="58" height="58" viewBox="0 0 58 58"><circle cx="29" cy="29" r="26" fill="none" stroke="#fff" stroke-width="3"/><circle cx="29" cy="29" r="12" fill="none" stroke="#fff" stroke-width="2.5"/><path d="M29 22v7l5 4" fill="none" stroke="#fff" stroke-width="2.5"/></svg>24-HOURS EMERGENCY<br>SERVICES</div>
  <div class="feature f-orange"><svg width="58" height="58" viewBox="0 0 58 58"><circle cx="29" cy="29" r="26" fill="none" stroke="#fff" stroke-width="3"/><path d="M18 32l11-12 11 12M22 30v10h14V30" fill="none" stroke="#fff" stroke-width="2.5"/></svg>LOCALLY OWNED &amp;<br>OPERATED</div>
  <div class="feature f-slate"><svg width="58" height="58" viewBox="0 0 58 58"><circle cx="29" cy="29" r="26" fill="none" stroke="#fff" stroke-width="3"/><circle cx="29" cy="26" r="7" fill="none" stroke="#fff" stroke-width="2.5"/><path d="M18 42c2-7 20-7 22 0" fill="none" stroke="#fff" stroke-width="2.5"/></svg>PROFESSIONAL WORK</div>
  <div class="feature f-green"><svg width="58" height="58" viewBox="0 0 58 58"><circle cx="29" cy="29" r="26" fill="none" stroke="#fff" stroke-width="3"/><rect x="20" y="17" width="18" height="24" fill="none" stroke="#fff" stroke-width="2.5"/><path d="M24 24h10M24 29h10M24 34h6" stroke="#fff" stroke-width="2"/></svg>FREE ESTIMATES</div>
</div>

<div class="section-title abs" style="left:0;top:1046px;width:1200px">
  <h2>OUR SERVICES</h2>
  <div class="kicker"><span class="rule l"></span>WHO WE PROVIDE<span class="rule r"></span></div>
</div>

<svg width="0" height="0" style="position:absolute"><defs>
  <symbol id="svc-icon" viewBox="0 0 80 80"><circle cx="40" cy="40" r="38" fill="#8dc63f"/><circle cx="40" cy="40" r="30" fill="none" stroke="#fff" stroke-width="2.5"/><circle cx="40" cy="34" r="11" fill="none" stroke="#fff" stroke-width="2.5"/><path d="M40 45v14M32 59h16" stroke="#fff" stroke-width="2.5"/></symbol>
</defs></svg>

<article class="service-card abs" style="left:126px;top:1182px"><svg class="service-icon"><use href="#svc-icon"/></svg><h3>Tree Pruning</h3><div class="service-photo" role="img" aria-label="Gloved hands pruning a bare branch with shears against a blue sky" style="background:linear-gradient(160deg,#cfe0f2,#7d98c0 60%,#5a4a3e)"></div></article>
<article class="service-card abs" style="left:450px;top:1182px"><svg class="service-icon"><use href="#svc-icon"/></svg><h3>Tree Removal</h3><div class="service-photo" role="img" aria-label="Worker cutting a tree stump with a chainsaw" style="background:linear-gradient(160deg,#6a5a3a,#4b3d29 55%,#8a6d4a)"></div></article>
<article class="service-card abs" style="left:774px;top:1182px"><svg class="service-icon"><use href="#svc-icon"/></svg><h3>Tree Preservation</h3><div class="service-photo" role="img" aria-label="Two arborists inspecting a tree trunk in a forest" style="background:linear-gradient(160deg,#5a5236,#7b6a4a 55%,#3d3a28)"></div></article>
<article class="service-card abs" style="left:126px;top:1624px"><svg class="service-icon"><use href="#svc-icon"/></svg><h3>Emergency Services</h3><div class="service-photo" role="img" aria-label="Fallen tree lying across a green lawn after a storm" style="background:linear-gradient(160deg,#6e7d55,#4a6a33 55%,#7a8a5a)"></div></article>
<article class="service-card abs" style="left:450px;top:1624px"><svg class="service-icon"><use href="#svc-icon"/></svg><h3>Stump Grinding</h3><div class="service-photo" role="img" aria-label="Workers feeding a log into a stump grinding machine" style="background:linear-gradient(160deg,#3a352e,#5a4a38 55%,#2c2822)"></div><svg class="abs" style="left:134px;top:310px" width="46" height="46" viewBox="0 0 46 46"><circle cx="23" cy="23" r="23" fill="#f8ab35"/><path d="M23 14v18M14 23h18" stroke="#fff" stroke-width="3"/></svg></article>
<article class="service-card abs" style="left:774px;top:1624px"><svg class="service-icon"><use href="#svc-icon"/></svg><h3>Emergency Tree Services</h3><div class="service-photo" role="img" aria-label="Uprooted trees leaning across a forest clearing" style="background:linear-gradient(160deg,#9aa68a,#5e6f48 55%,#8c9a78)"></div></article>

<div class="about-head abs" style="left:124px;top:2156px">
  <h2>ABOUT US</h2>
  <div class="kicker">WHO WE ARE<span class="rule r" style="margin-left:6px"></span></div>
</div>
<div class="about-copy abs" style="left:124px;top:2260px">
  <p>At Verdell Tree Care, we are more than just a tree service company, we are stewards of our beautiful trees. With a passion deeply rooted in arboriculture, we embark on a mission to promote the health, beauty, and safety of your trees and landscapes.</p>
  <p>Whether it's expert tree trimming to enhance aesthetics, meticulous tree removal to mitigate hazards, or comprehensive tree health assessments to ensure safety, we approach each task with unwavering dedication and attention to detail.</p>
</div>
<a class="btn-green abs" style="left:124px;top:2484px;width:156px;height:50px;line-height:50px;font-size:12px">READ MORE</a>
<div class="abs" role="img" aria-label="Tall tree and green foliage photo panel" style="left:728px;top:2186px;width:350px;height:348px;background:linear-gradient(180deg,#5f8a3a,#3f6a2a 50%,#6f9a45)"></div>

<section class="cta abs" role="img" aria-label="Chainsaw cutting through a log with sawdust flying, blending into green">
</section>
<div class="abs" style="left:72px;top:2756px">
  <h2 class="cta-h" style="color:#fff;font-size:43px;font-weight:600;line-height:1.3">CALL US TODAY TO SEE HOW<br>WE CAN HELP YOU WITH ALL<br>OF YOUR TREE NEEDS:</h2>
  <a class="btn-white" style="margin:22px 0 0 6px">CONTACT US</a>
</div>

<div class="section-title abs" style="left:0;top:3250px;width:1200px">
  <h2>OUR BLOG</h2>
  <div class="kicker"><span class="rule l" style="width:56px"></span>LATEST NEWS<span class="rule r" style="width:56px"></span></div>
</div>

<article class="post-card abs" style="left:148px;top:3372px"><div class="post-photo" role="img" aria-label="Arborists in safety vests working in a pine forest" style="background:linear-gradient(160deg,#6b6a50,#4d5a35 55%,#8a7a55)"></div><div class="post-body"><div class="post-date"><i></i>Apr 25, 2022</div><h3>Lorem ipsum dolor sit amet, consectetur elit dol</h3><p>Lorem ipsum dolor sit amet, con sectetur adipiscing elit, sed do ei</p><a class="btn-green">Read More</a></div></article>
<article class="post-card abs" style="left:460px;top:3372px"><div class="post-photo" role="img" aria-label="Crew clearing fallen branches in woodland" style="background:linear-gradient(160deg,#5a5a42,#7a6a4a 55%,#4a5233)"></div><div class="post-body"><div class="post-date"><i></i>Apr 25, 2022</div><h3>Lorem ipsum dolor sit amet, consectetur elit dol</h3><p>Lorem ipsum dolor sit amet, con sectetur adipiscing elit, sed do ei</p><a class="btn-green">Read More</a></div></article>
<article class="post-card abs" style="left:772px;top:3372px"><div class="post-photo" role="img" aria-label="Chainsaw cutting into a tree stump" style="background:linear-gradient(160deg,#9a7a5a,#6a4a32 55%,#b89a7a)"></div><div class="post-body"><div class="post-date"><i></i>Apr 25, 2022</div><h3>Lorem ipsum dolor sit amet, consectetur elit dol</h3><p>Lorem ipsum dolor sit amet, con sectetur adipiscing elit, sed do ei</p><a class="btn-green">Read More</a></div></article>

<div class="dots abs" style="left:550px;top:3912px"><span class="on"></span><span></span><span></span><span></span></div>

<div class="contact-photo abs" role="img" aria-label="Misty forest of tall trees with ferns"></div>
<div class="about-head abs" style="left:628px;top:4046px">
  <h2>CONTACT US</h2>
  <div class="kicker">GET IN TOUCH<span class="rule r" style="margin-left:6px;width:130px"></span></div>
</div>
<div class="field abs" style="left:632px;top:4178px;width:224px;height:44px">First Name:</div>
<div class="field abs" style="left:874px;top:4178px;width:224px;height:44px">Last Name:</div>
<div class="field abs" style="left:632px;top:4244px;width:224px;height:44px">Phone:</div>
<div class="field abs" style="left:874px;top:4244px;width:224px;height:44px">Email:</div>
<div class="field abs" style="left:632px;top:4310px;width:466px;height:142px;padding-top:24px">Mesage:</div>
<a class="btn-green abs" style="left:632px;top:4488px;width:168px;height:50px;line-height:50px;font-size:16px">SUBMIT</a>

<footer class="site-footer abs"></footer>
<div class="newsletter abs">
  <h3>Our Newsletter Sign Up</h3>
  <div class="nl-form">Enter Email Address<span>SIGNUP</span></div>
</div>
<div class="abs" style="left:204px;top:4870px">
  <h4 class="foot-h">QUICK LINKS</h4>
  <ul class="quick-links" style="margin-top:16px"><li>Home</li><li>About Us</li><li>Services</li><li>Blog</li><li>Contact Us</li></ul>
</div>
<div class="footer-brand abs"><span class="brand-mark"></span><span style="font-size:34px">Verdell Tree Care</span></div>
<div class="abs" style="left:780px;top:4870px">
  <h4 class="foot-h" style="margin-bottom:18px">CONTACT US</h4>
  <div class="contact-item"><i></i><div>CALL US<br>(555) 014-2739</div></div>
  <div class="contact-item"><i></i><div>EMAIL US<br>hello@verdellmail.com</div></div>
  <div class="contact-item"><i></i><div>Address line here dummy<br>Address line here</div></div>
</div>
<div class="bottom-bar abs"><span style="position:absolute;left:76px;top:17px">Copyright ©2024- All Rights Reserved by Company name</span><div class="socials"><span></span><span></span><span></span><span></span></div></div>

</body>
</html>
```